Social Media App Needs PPT Template

We need a PowerPoint template for a new social media company based in the DC area called "Bold Ledger." We provide an interactive digital platform for executives to share actionable advice. We would like to see designs that use our orange logo color as an accent, but are mainly grey, white, and black. The final design should communicate clean, chic, modern, and professional.

Target Market(s)

Executives

Industry/Entity Type

Information Technology

Font styles to use
Sans Serif

Colors
f78f20
fbe7d2
ffffff
000000
e8e8e8
757575

Requirements
Must have
• My project must have title page and many options for the body of the ppt (graphs, tables, etc). It also needs to be easy to modify. I must have someone who is experienced in creating powerpoint templates.
Nice to have
• It would be nice to have a very modern and clean design that includes the logo on every page, but still leaves a lot of room for the content of the slide
Should not have
• My design project should not look to busy.

```html
<!DOCTYPE html>
<html lang="en">
<head>
<meta charset="utf-8">
<title>Bold Ledger – Social Studies</title>
<link rel="stylesheet" href="https://fonts.googleapis.com/css2?family=Open+Sans:wght@700;800&display=swap">
<style>
  :root {
    --white: #ffffff;
    --black: #000000;
    --orange: #f78f20;
    --peach: #fbcf9a;
    --cream: #fbe7d2;
    --tan: #efb978;
    --brown: #b97b4b;
    --red: #e0393b;
    --green: #86c23a;
    --purple: #8a5cb0;
    --cyan: #12b3d6;
    --amber: #f89a1c;
    --blue: #1f7fd0;
  }
  html, body {
    margin: 0;
    padding: 0;
    overflow: hidden;
    background: var(--white);
  }
  .slide {
    position: relative;
    width: 1200px;
    height: 900px;
    overflow: hidden;
    background: var(--white);
    font-family: "Open Sans", Arial, sans-serif;
  }
  .slide-art { position: absolute; inset: 0; width: 1200px; height: 900px; }
  .topic-label {
    fill: var(--white);
    font-weight: 700;
    font-size: 17px;
    text-anchor: middle;
    dominant-baseline: middle;
    letter-spacing: -0.3px;
  }
  .hub-label {
    fill: var(--white);
    font-weight: 800;
    font-size: 42px;
    text-anchor: middle;
  }
  .brand-name {
    fill: var(--black);
    font-weight: 800;
    font-size: 30px;
    text-anchor: middle;
    dominant-baseline: middle;
  }
  .c-red { fill: var(--red); }
  .c-green { fill: var(--green); }
  .c-purple { fill: var(--purple); }
  .c-cyan { fill: var(--cyan); }
  .c-amber { fill: var(--amber); }
</style>
</head>
<body>
<div class="slide">
  <svg class="slide-art" viewBox="0 0 1500 1125" xmlns="http://www.w3.org/2000/svg">
    <defs>
      <radialGradient id="hub-fill" cx="40%" cy="30%" r="75%">
        <stop offset="0" stop-color="#3aa0ea"/>
        <stop offset="1" stop-color="#176bb8"/>
      </radialGradient>
      <path id="arrow" d="M0,-45 L30,-8 L13,-8 L13,45 L-13,45 L-13,-8 L-30,-8 Z"/>
    </defs>

    <!-- side bands -->
    <g class="frame-bands">
      <polygon points="0,670 72,1125 0,1125" fill="var(--orange)"/>
      <polygon points="1150,0 1500,0 1500,1125 1090,1125 1362,800" fill="var(--orange)"/>
      <polygon points="1300,565 1362,800 1150,1050" fill="var(--peach)"/>
      <polygon points="1325,0 1472,0 1412,612" fill="var(--brown)"/>
      <polygon points="1472,0 1500,0 1500,892 1447,900 1412,612" fill="var(--tan)"/>
      <polygon points="1412,612 1447,900 1388,900" fill="var(--cream)"/>
    </g>

    <!-- arrows -->
    <g class="spokes">
      <use href="#arrow" class="c-red"    transform="translate(578 528) rotate(0) translate(0 -185)"/>
      <use href="#arrow" class="c-green"  transform="translate(578 528) rotate(36) translate(0 -185)"/>
      <use href="#arrow" class="c-purple" transform="translate(578 528) rotate(72) translate(0 -185)"/>
      <use href="#arrow" class="c-cyan"   transform="translate(578 528) rotate(108) translate(0 -185)"/>
      <use href="#arrow" class="c-amber"  transform="translate(578 528) rotate(144) translate(0 -185)"/>
      <use href="#arrow" class="c-red"    transform="translate(578 528) rotate(180) translate(0 -185)"/>
      <use href="#arrow" class="c-green"  transform="translate(578 528) rotate(216) translate(0 -185)"/>
      <use href="#arrow" class="c-purple" transform="translate(578 528) rotate(252) translate(0 -185)"/>
      <use href="#arrow" class="c-cyan"   transform="translate(578 528) rotate(288) translate(0 -185)"/>
      <use href="#arrow" class="c-amber"  transform="translate(578 528) rotate(324) translate(0 -185)"/>
    </g>

    <!-- topic circles -->
    <g class="topics">
      <circle class="c-red" cx="578" cy="168" r="85"/><text class="topic-label" x="578" y="172">History</text>
      <circle class="c-green" cx="790" cy="238" r="85"/><text class="topic-label" x="790" y="242">Geography</text>
      <circle class="c-purple" cx="922" cy="418" r="85"/><text class="topic-label" x="922" y="422">Archaeology</text>
      <circle class="c-cyan" cx="922" cy="640" r="85"/><text class="topic-label" x="922" y="644">Religion</text>
      <circle class="c-amber" cx="790" cy="820" r="85"/><text class="topic-label" x="790" y="824">Politics</text>
      <circle class="c-red" cx="578" cy="888" r="85"/><text class="topic-label" x="578" y="892">Philosophy</text>
      <circle class="c-green" cx="366" cy="820" r="85"/><text class="topic-label" x="366" y="824">Economics</text>
      <circle class="c-purple" cx="235" cy="640" r="85"/><text class="topic-label" x="235" y="644">Sociology</text>
      <circle class="c-cyan" cx="235" cy="418" r="85"/><text class="topic-label" x="235" y="422">Anthropology</text>
      <circle class="c-amber" cx="366" cy="238" r="85"/><text class="topic-label" x="366" y="242">Psychology</text>
    </g>

    <!-- hub -->
    <g class="hub">
      <circle cx="578" cy="528" r="106" fill="url(#hub-fill)"/>
      <text class="hub-label" x="578" y="522">Social</text>
      <text class="hub-label" x="578" y="572">Studies</text>
    </g>

    <!-- brand badge -->
    <g class="brand-badge">
      <circle cx="1360" cy="998" r="104" fill="var(--white)"/>
      <text class="brand-name" x="1360" y="1000">Bold Ledger</text>
    </g>
  </svg>
</div>
</body>
</html>
```